Kestrel Baseball & Softball Camp 2017

Design a flyer that will promote our 2017 summer camp for boys and girls softball.

Weeks of
July 10th - 14th
July 17th - 21st.

Players ages 5 - 11.
Full day = 9:30am - 2:30pm half day = 9:30am - 11:30am.
$295 / full day : $195/ half day

Hosted by "Kestrel Baseball" affiliated with the Harbor Comets Travel Baseball & Softball Club and the Maple Ridge Youth League,

Camp Location MRYL, Route 9C Birch Hollow.

PHone 555-240-7813, email info@kestrelball.example

The color should be "Red white and blue color scheme" with dates and location standing out. Kestrel Logo should be prominent MRYL and Comets smaller and secondary.

Feel free to use stock photo's if available. visit www.harborcomets.example for more pictures and there are links for the 2017 summer camp there with possibly some more information.

Target Market(s)

to catch the eye of parents of players ages 5 - 11 already at little league or shopping in local stores

Colors
ec1f27
0355a3
ffffff

Requirements
Must have
• red white and blue design,
• Kestrel logo and summer camp prominent so it catches the eye and explains what it is right away.
• the comets and maple ridge logo's a the bottom showing the affiliation.
Nice to have
• stock photo's or something showing players having a great time or a beautiful ballpark
Should not have
• to much clutter or hard to figure out what it's for

```html
<!DOCTYPE html>
<html lang="en">
<head>
<meta charset="utf-8">
<title>Kestrel Softball Summer Camp 2017</title>
<link rel="stylesheet" href="https://fonts.googleapis.com/css2?family=Bebas+Neue&family=Oswald:wght@400;500;700&family=Kaushan+Script&family=Yellowtail&display=swap">
<style>
  :root {
    --red: #d9262e;
    --navy: #1f3a68;
    --blue: #0355a3;
    --white: #ffffff;
    --ink: #1d1d1d;
    --dirt-light: #a97457;
    --dirt-dark: #6f4632;
    --rule: #8c8c8c;
  }
  * { margin: 0; padding: 0; box-sizing: border-box; }
  html, body { width: 817px; height: 1200px; overflow: hidden; background: var(--white); }
  .flyer {
    position: relative; width: 800px; height: 1175px;
    transform: scale(1.02125); transform-origin: top left;
    overflow: hidden; background: var(--white);
    font-family: "Oswald", sans-serif;
  }
  .shapes { position: absolute; inset: 0; }
  .abs { position: absolute; }

  .brand { left: 40px; top: 80px; display: flex; align-items: center; gap: 10px; }
  .brand-dot { width: 26px; height: 26px; border-radius: 50%; background: var(--navy); }
  .brand-name { font-family: "Bebas Neue", sans-serif; font-size: 62px; color: var(--red); line-height: 1; }

  .kicker { left: 58px; top: 282px; font-family: "Yellowtail", cursive; font-size: 62px; line-height: 1; color: var(--white); transform: rotate(-6deg); }
  .title { left: 46px; top: 362px; font-family: "Bebas Neue", sans-serif; font-weight: 400; font-size: 150px; line-height: 1; letter-spacing: 1px; transform: rotate(-3deg) scaleX(0.93); transform-origin: left bottom; white-space: nowrap; }
  .title-summer { color: var(--white); }
  .title-camp { color: var(--red); }
  .year { left: 742px; top: 326px; font-family: "Bebas Neue", sans-serif; font-size: 60px; line-height: 1; color: var(--white); transform: rotate(90deg); transform-origin: left top; letter-spacing: 2px; white-space: nowrap; }
  .audience { left: 448px; top: 500px; font-family: "Yellowtail", cursive; font-size: 24px; color: var(--white); transform: rotate(-5deg); }

  .dates { left: 80px; top: 615px; font-family: "Bebas Neue", sans-serif; font-size: 42px; line-height: 44px; color: var(--white); letter-spacing: 1px; }

  .hosts { left: 415px; top: 594px; font-family: "Oswald", sans-serif; font-weight: 500; font-size: 11.5px; line-height: 28px; letter-spacing: 1.2px; color: var(--navy); text-transform: uppercase; }
  .partner-name { left: 640px; top: 582px; font-family: "Bebas Neue", sans-serif; font-size: 42px; color: var(--red); line-height: 1; }
  .partner-badge { left: 645px; top: 650px; width: 60px; height: 68px; background: #e9efd8; border: 2px solid #5b8f3a; border-radius: 6px; }

  .hours { left: 108px; top: 815px; font-family: "Bebas Neue", sans-serif; font-size: 27px; line-height: 31px; color: var(--red); letter-spacing: .5px; }
  .cost-label { left: 118px; top: 923px; font-family: "Kaushan Script", cursive; font-size: 20px; color: var(--navy); }
  .cost { left: 222px; top: 915px; font-family: "Bebas Neue", sans-serif; font-size: 27px; line-height: 31px; color: var(--navy); letter-spacing: .5px; }

  .ages-label { left: 478px; top: 862px; font-family: "Bebas Neue", sans-serif; font-size: 40px; line-height: 44px; color: var(--navy); letter-spacing: 1px; }
  .ages-badge { left: 607px; top: 837px; width: 132px; height: 132px; border-radius: 50%; background: var(--navy); color: var(--white); display: flex; align-items: center; justify-content: center; font-family: "Bebas Neue", sans-serif; font-size: 44px; letter-spacing: 1px; }

  .gear-photo { left: 0; top: 1010px; width: 200px; height: 165px; background: radial-gradient(circle at 95px 90px, #e8ee3a 0 62px, #b58458 64px 100%); }
  .cta { left: 205px; top: 1035px; font-family: "Kaushan Script", cursive; font-size: 32px; line-height: 38px; color: var(--red); transform: rotate(-8deg); }

  .info-label { font-family: "Kaushan Script", cursive; font-size: 17px; color: var(--navy); }
  .info-text { font-family: "Oswald", sans-serif; font-weight: 500; font-size: 14.5px; line-height: 22px; color: var(--ink); text-transform: uppercase; }
  .location-label { left: 372px; top: 1042px; }
  .location-text { left: 372px; top: 1070px; }
  .contact-label { left: 585px; top: 1042px; }
  .contact-text { left: 585px; top: 1070px; }
</style>
</head>
<body>
<main class="flyer">
  <svg class="shapes" viewBox="0 0 800 1175" width="800" height="1175">
    <defs>
      <linearGradient id="dirt" x1="0" y1="0" x2="1" y2="1">
        <stop offset="0" stop-color="#a97457"/>
        <stop offset="1" stop-color="#6f4632"/>
      </linearGradient>
    </defs>
    <polygon role="img" aria-label="Photo of a baseball infield with chalk lines around home plate" points="300,0 800,0 800,515 580,560 0,560 0,235 245,205" fill="url(#dirt)"/>
    <polygon class="band-navy" points="240,352 668,312 592,558 0,598 0,470" fill="var(--navy)"/>
    <polygon class="band-red" points="0,545 440,490 362,785 0,825" fill="var(--red)"/>
    <line x1="22" y1="548" x2="412" y2="537" stroke="var(--white)" stroke-width="1.5" stroke-dasharray="9 6"/>
    <line x1="345" y1="785" x2="800" y2="700" stroke="var(--rule)" stroke-width="1.5" stroke-dasharray="9 6"/>
    <g fill="none" stroke="var(--red)" stroke-width="3">
      <circle cx="81" cy="846" r="13"/>
      <line x1="81" y1="846" x2="81" y2="838"/>
      <line x1="76" y1="829" x2="86" y2="829"/>
    </g>
    <g fill="var(--navy)">
      <circle cx="440" cy="872" r="5"/>
      <rect x="434" y="879" width="12" height="18" rx="2"/>
      <rect x="435" y="895" width="4" height="14"/><rect x="441" y="895" width="4" height="14"/>
      <circle cx="460" cy="872" r="5"/>
      <polygon points="460,878 468,900 452,900"/>
      <rect x="455" y="899" width="4" height="10"/><rect x="461" y="899" width="4" height="10"/>
    </g>
    <circle cx="188" cy="941" r="15" fill="var(--navy)"/>
    <text x="188" y="948" text-anchor="middle" font-family="Oswald, sans-serif" font-weight="700" font-size="19" fill="var(--white)">$</text>
    <path d="M354 1034 a9 9 0 0 1 9 9 c0 7 -9 16 -9 16 s-9 -9 -9 -16 a9 9 0 0 1 9 -9z" fill="var(--navy)"/>
    <circle cx="354" cy="1043" r="3.5" fill="var(--white)"/>
    <g fill="var(--navy)">
      <rect x="564" y="1036" width="14" height="22" rx="2"/>
      <rect x="566" y="1028" width="2" height="9"/>
    </g>
    <rect x="567" y="1040" width="8" height="6" fill="var(--white)"/>
  </svg>

  <div class="abs brand"><span class="brand-name">Kestrel</span><span class="brand-dot"></span></div>

  <div class="abs kicker">softball</div>
  <h1 class="abs title"><span class="title-summer">SUMMER</span><span class="title-camp">CAMP</span></h1>
  <div class="abs year">2017</div>
  <div class="abs audience">for boys and girls</div>

  <div class="abs dates">WEEKS OF<br>JULY 10TH - 14TH<br>JULY 17TH - 21ST.</div>

  <p class="abs hosts">Hosted by "Kestrel Baseball"<br>Affiliated with the Harbor Comets<br>Travel Baseball &amp; Softball Club and<br>the Maple Ridge Youth League</p>
  <div class="abs partner-name">Comets</div>
  <div class="abs partner-badge" role="img" aria-label="Maple Ridge Youth League badge"></div>

  <div class="abs hours">FULL DAY = 9:30AM - 2:30PM<br>HALF DAY = 9:30AM - 11:30AM</div>
  <div class="abs cost-label">Cost:</div>
  <div class="abs cost">$295 / FULL DAY<br>$195/ HALF DAY</div>

  <div class="abs ages-label">PLAYERS<br>AGES</div>
  <div class="abs ages-badge">5 - 11</div>

  <div class="abs gear-photo" role="img" aria-label="Photo of a yellow softball with a glove and bat"></div>
  <div class="abs cta">Register<br>today!</div>

  <div class="abs info-label location-label">Camp Location:</div>
  <div class="abs info-text location-text">Camp Location MRYL,<br>Route 9C Birch Hollow.</div>
  <div class="abs info-label contact-label">Contact:</div>
  <div class="abs info-text contact-text">Phone 555-240-7813, Email<br>info@kestrelball.example</div>
</main>
</body>
</html>
```